Modernize Website: marcusfellwright.net

I am a novelist with an older-generation website at: marcusfellwright.net.

I am hoping to refresh this outdated website with a new, responsive redesign. I would prefer to host the code myself, and edit using Adobe Dreamweaver. So I’m not looking to use a hosted site builder like Plexo. Nor am I looking to use a CMS like Pagecraft.

In order to simplify the old site, there are a number of sections I’ll be looking to remove during this redesign. These are shown in the "MF Site Redesign" attachment. I can also provide imagery for new content (another book series in addition to the existing one), as well as higher-resolution imagery (if needed) of the old content.

Happy to answer any further questions.
Updates

I've uploaded a ZIP file containing high-res artwork associated with the new trilogy of books.

Target Market(s)

Readers of epic fantasy novels such as H.W.B. Castellane's THE WARDEN OF THE VALES, Harold P.Q. Ventris's A CROWN OF ASH AND RAIN, Victor Halloway's THE GATE OF STARS, or Dennis Vale's BLADE OF MERIVANE.

Industry/Entity Type

Entertainment

Coding

Coded - Design and coding required

Number of Pages Required

5+ page

Font styles to use
Serif
Decorative

Colors

Designer to choose colors to be used in the design.

Requirements
Must have
• I'm looking for a responsive design that displays nicely on both mobile and desktop devices. Existing site contains multiple pages, but these can obviously be combined into fewer pages (or even one) by divisions such as tabs, sections, and/or modal windows. See marcusfellwright.net for current content and "MF Site Redesign" attachment for content to be removed at this time.
Nice to have
• The ability to fulfill orders of autographed books directly from the website. I currently use Coinlo to do this, but it would be nice to incorporate a more comprehensive merchant service at a reasonable rate.
Should not have
• I'd like to host and control the site code myself. So please don't use a hosted web builder like Plexo, or a cloud-based CMS like Pagecraft.

```html
<!DOCTYPE html>
<html lang="en">
<head>
<meta charset="utf-8">
<title>Author – News | Marcus Fellwright</title>
<link href="https://fonts.googleapis.com/css2?family=Cinzel:wght@400;700&family=Roboto:wght@400;500&display=swap" rel="stylesheet">
<style>
  :root {
    --black: #000000;
    --night: #0b080b;
    --white: #ffffff;
    --red: #e3101e;
    --red-deep: #a1000c;
    --link-red: #e41b23;
    --text-soft: #e9e9e9;
    --hero-top: #4a4552;
    --hero-mid: #6b5a55;
    --hero-low: #1c1417;
  }
  * { box-sizing: border-box; margin: 0; padding: 0; }
  html, body { width: 1200px; height: 2163px; overflow: hidden; }
  body {
    position: relative;
    background: var(--night);
    font-family: "Roboto", Arial, sans-serif;
    color: var(--white);
  }
  a { color: inherit; text-decoration: none; }

  /* Header */
  .site-header {
    position: absolute; left: 0; top: 0; width: 1200px; height: 121px;
    background: var(--black); z-index: 5;
  }
  .brand {
    position: absolute; left: 101px; top: 40px;
    font-family: "Cinzel", Georgia, serif; font-weight: 400;
    font-size: 22px; line-height: 24px; letter-spacing: 1px; color: var(--white);
  }
  .main-nav {
    position: absolute; top: 64px; left: 529px;
    display: flex; gap: 0; font-size: 15px; font-weight: 500;
  }
  .main-nav a { position: absolute; white-space: nowrap; }
  .main-nav .caret { display: inline-block; width: 7px; height: 7px; margin-left: 5px;
    border-right: 1.5px solid var(--white); border-bottom: 1.5px solid var(--white);
    transform: translateY(-3px) rotate(45deg); }
  .login-btn {
    position: absolute; left: 991px; top: 57px; width: 110px; height: 35px;
    border-radius: 18px; background: linear-gradient(var(--red), var(--red-deep));
    font-size: 15px; font-weight: 500; display: flex; align-items: center; justify-content: center; gap: 7px;
  }

  /* Dropdown */
  .submenu {
    position: absolute; left: 697px; top: 121px; width: 155px; height: 193px;
    background: var(--black); z-index: 6; font-size: 15px; font-weight: 500;
  }
  .submenu a { position: absolute; left: 21px; }
  .submenu .active-band {
    position: absolute; left: 0; top: 46px; width: 155px; height: 39px;
    background: linear-gradient(var(--red-deep), var(--red) 45%, var(--red-deep));
  }

  /* Hero & backdrop */
  .backdrop {
    position: absolute; left: 0; top: 121px; width: 1200px; height: 1650px;
    background:
      radial-gradient(ellipse 200px 120px at 0 1000px, rgba(220,90,30,.35), transparent),
      radial-gradient(ellipse 160px 140px at 1200px 1150px, rgba(230,110,40,.35), transparent),
      linear-gradient(var(--hero-top) 0, var(--hero-mid) 380px, var(--hero-low) 560px, #120c10 900px, #1a0f0e 1500px, #0f0a0a 1650px);
  }
  .page-title {
    position: absolute; left: 110px; top: 298px;
    font-family: "Cinzel", Georgia, serif; font-weight: 700; font-size: 88px; line-height: 1;
    color: var(--white); text-shadow: 0 0 14px var(--red), 0 0 28px var(--red-deep);
  }

  /* Modal */
  .news-modal {
    position: absolute; left: 89px; top: 766px; width: 1022px; height: 871px;
    background: var(--black); border: 3px solid var(--red);
  }
  .close-btn {
    position: absolute; left: 960px; top: -3px; width: 62px; height: 62px;
    border-radius: 50%; background: var(--red);
  }
  .close-btn svg { position: absolute; left: 19px; top: 19px; }
  .news-title {
    position: absolute; left: 78px; top: 74px;
    font-family: "Cinzel", Georgia, serif; font-weight: 700; font-size: 34px; letter-spacing: .5px;
  }
  .news-date {
    position: absolute; left: 78px; top: 150px;
    font-family: "Cinzel", Georgia, serif; font-weight: 700; font-size: 23px;
  }
  .news-body {
    position: absolute; left: 78px; top: 209px; width: 862px;
    font-size: 13px; line-height: 24.5px; color: var(--text-soft);
  }
  .news-body p + p { margin-top: 24px; }
  .news-photo {
    position: absolute; left: 267px; top: 391px; width: 475px; height: 338px;
    border: 3px solid var(--white);
    background: linear-gradient(110deg, #1d1a22 0 32%, #6d6258 45%, #2a2a2e 58%, #3a3f48 80%, #1b1c20);
  }
  .news-link {
    position: absolute; left: 0; top: 767px; width: 1016px; text-align: center;
    font-size: 16px; color: var(--link-red); text-decoration: underline;
  }

  /* Footer */
  .site-footer {
    position: absolute; left: 0; top: 1771px; width: 1200px; height: 392px; background: var(--black);
  }
  .footer-brand {
    position: absolute; left: 0; top: 67px; width: 1200px; text-align: center;
    font-family: "Cinzel", Georgia, serif; font-weight: 400; font-size: 22px; letter-spacing: 1px;
  }
  .social { position: absolute; top: 170px; left: 513px; display: flex; gap: 12px; }
  .social a {
    width: 50px; height: 50px; border-radius: 50%; background: var(--white); color: var(--red);
    display: flex; align-items: center; justify-content: center;
    font-family: "Roboto", Arial, sans-serif; font-size: 10px; font-weight: 500;
  }
  .footer-nav {
    position: absolute; left: 0; top: 2030px; width: 1200px; text-align: center; font-size: 14px;
  }
  .footer-nav, .copyright { top: auto; }
  .footer-links { position: absolute; top: 260px; left: 0; width: 1200px; text-align: center; font-size: 14px; }
  .footer-links span { margin: 0 20px; }
  .copyright { position: absolute; top: 306px; left: 0; width: 1200px; text-align: center; font-size: 13px; }
  .copyright span { margin: 0 12px; }
</style>
</head>
<body>

<header class="site-header">
  <a class="brand" href="#">MARCUS FELLWRIGHT</a>
  <nav class="main-nav">
    <a href="#" style="left:0">HOME</a>
    <a href="#" style="left:71px">NOVELS<span class="caret"></span></a>
    <a href="#" style="left:171px">WORLD<span class="caret"></span></a>
    <a href="#" style="left:263px">AUTHOR<span class="caret"></span></a>
    <a href="#" style="left:365px">CONTACT</a>
  </nav>
  <a class="login-btn" href="#">
    <svg width="11" height="13" viewBox="0 0 11 13"><rect x="0" y="5" width="11" height="8" rx="1.5" fill="#fff"/><path d="M2.5 5V3.5a3 3 0 0 1 6 0V5" fill="none" stroke="#fff" stroke-width="1.8"/></svg>
    LOGIN
  </a>
</header>

<nav class="submenu">
  <div class="active-band"></div>
  <a href="#" style="top:12px">Biography</a>
  <a href="#" style="top:56px">News</a>
  <a href="#" style="top:98px">Events</a>
  <a href="#" style="top:129px">Interviews</a>
  <a href="#" style="top:159px">Q &amp; A</a>
</nav>

<div class="backdrop" role="img" aria-label="Fantasy scene: a warrior facing a dragon beside a ruined stone tower under stormy skies, fading into a dark, ember-lit battlefield"></div>
<h1 class="page-title">AUTHOR</h1>

<article class="news-modal">
  <a class="close-btn" href="#" aria-label="Close">
    <svg width="24" height="24" viewBox="0 0 24 24"><path d="M4 4L20 20M20 4L4 20" stroke="#fff" stroke-width="5" stroke-linecap="round"/></svg>
  </a>
  <h2 class="news-title">UNBRIDLED DIGITAL RELEASE</h2>
  <h3 class="news-date">JUNE 24, 2013</h3>
  <div class="news-body">
    <p>Today marks the official ebook release of Unbridled from Iron Fern Press, featuring Marcus's short story Unyielding. Direct links to various digital sellers can be found below. This is the anthology compiled and edited by Corwin Ashdale, comprised of stories donated by a number of bestselling fantasy authors to help alleviate medical bills resulting from Corwin's second bout with cancer.</p>
    <p>Those who ordered hard copies of the exclusive anthology should receive them soon. For more information, review the official announcement at:</p>
  </div>
  <div class="news-photo" role="img" aria-label="Photo of the anthology hardcover standing on a signing table beside pens and other books"></div>
  <a class="news-link" href="#">http://ironfernpress.com/2013/06/ebook-published-unbridled</a>
</article>

<footer class="site-footer">
  <a class="footer-brand" href="#">MARCUS FELLWRIGHT</a>
  <div class="social">
    <a href="#">Circlo</a>
    <a href="#">Chirpa</a>
    <a href="#" aria-label="Email">
      <svg width="22" height="16" viewBox="0 0 22 16"><rect x="1.2" y="1.2" width="19.6" height="13.6" rx="2" fill="none" stroke="#e3101e" stroke-width="2.2"/><path d="M2 2.5L11 9.5L20 2.5" fill="none" stroke="#e3101e" stroke-width="2.2"/></svg>
    </a>
  </div>
  <nav class="footer-links">
    <a href="#">Home</a><span>|</span><a href="#">Novels</a><span>|</span><a href="#">World</a><span>|</span><a href="#">Author</a><span>|</span><a href="#">Contact</a>
  </nav>
  <p class="copyright">© Copyright 2018 Marcus Fellwright. All Rights Reserved<span>|</span><a href="#">Terms of Use</a><span>|</span><a href="#">Privacy Policy.</a></p>
</footer>

</body>
</html>
```